Organization and people consulting firm needs a website design

I need a website that promotes and explains the consulting service we will provide. The organization is called Bluefinch Advisory Partners. Our services include organization design, employee experience, change management, and executive coaching. I would like to see a simple clean and professional design, that reflects a modern and forward looking professional services company

Target Market(s)

Mid market and large companies

Industry/Entity Type

Management Consulting

Coding

Coded - Design and coding required

Number of Pages Required

5+ page

Font styles to use
Sans Serif

Colors

Designer to choose colors to be used in the design.

Requirements
Must have
• The following pages: Home, The Way We Work, What We Do, Our Founder, Insights, Contact.
• Search button.
• Hyper links (will be provided with main body text)
• Scrolling website with summaries at top level and links to more detail at lower level (like this website: veltracore.com)
• Company logo (uploaded)
• I have text for each of the pages that I can upload once the basic design is done
Should not have
• No clutter, keep the design clean

```html
<!DOCTYPE html>
<html lang="en">
<head>
<meta charset="utf-8">
<title>Bluefinch Advisory Partners</title>
<link rel="stylesheet" href="https://fonts.googleapis.com/css2?family=Cinzel:wght@400;600&family=Montserrat:wght@500;700&family=Open+Sans:wght@400;600;700&display=swap">
<style>
:root{
  --red:#d7062f;
  --red-soft:#e8717f;
  --ink:#222222;
  --grey-text:#7a7a7a;
  --mid-grey:#8d8d8d;
  --light-grey:#c9c9c9;
  --dot:#cfcfcf;
  --white:#ffffff;
  --footer:#333333;
}
*{box-sizing:border-box;margin:0;padding:0}
html,body{width:1200px;height:3243px;overflow:hidden}
body{position:relative;background:var(--white);font-family:"Open Sans",Arial,sans-serif;color:#555}
.abs{position:absolute}
/* hero */
.hero{left:0;top:0;width:1200px;height:660px;background:linear-gradient(135deg,#5b5e63 0%,#3a3c40 45%,#6e7074 75%,#2e3033 100%)}
.brand{left:175px;top:44px;display:flex;align-items:center;gap:10px;color:var(--white);font-family:"Open Sans",Arial,sans-serif;font-weight:600;font-size:15px;line-height:1}
.brand-mark{width:26px;height:26px;border-radius:50%;background:var(--white)}
.nav{left:478px;top:53px;display:flex;gap:24px;font-family:"Open Sans",Arial,sans-serif;font-size:13px;font-weight:600;color:var(--white)}
.hero-num{left:172px;top:205px;font-family:"Montserrat",Arial,sans-serif;font-weight:700;font-size:36px;color:var(--white)}
.hero-title{left:272px;top:230px;color:var(--white);font-family:"Cinzel",Georgia,serif;font-weight:400;font-size:31px;line-height:46px;letter-spacing:1px}
.hero-title span{display:block;font-size:39px}
.dots{display:flex;flex-direction:column;gap:9px}
.dots i{display:block;width:11px;height:11px;border-radius:50%;background:var(--dot)}
.dots i.on{background:var(--red)}
.hero .dots i{background:var(--white)}
.slider{left:558px;top:600px;display:flex;align-items:center;gap:6px}
.slider b{width:18px;height:18px;border-radius:50%;background:var(--white);display:flex;align-items:center;justify-content:center}
.slider i{width:8px;height:8px;border-radius:50%;background:#bbb}
.slider i.on{background:var(--white)}
/* section heads */
.sec-num{font-family:"Montserrat",Arial,sans-serif;font-weight:700;font-size:34px;color:var(--ink);line-height:1}
.sec-title{font-family:"Montserrat",Arial,sans-serif;font-weight:700;font-size:34px;line-height:45px;color:var(--grey-text);text-transform:uppercase;white-space:nowrap}
.copy{font-size:14px;line-height:25px;color:#555}
.copy p+p{margin-top:10px}
/* what we do */
.service{width:250px;color:var(--white)}
.service h3{font-family:"Open Sans",Arial,sans-serif;font-weight:600;font-size:15px;margin-bottom:6px}
.service p{font-size:11px;line-height:16px}
.service.left{text-align:right}
.icon-ring{width:54px;height:54px;border:2px solid var(--white);border-radius:50%}
/* founder */
.founder-name{left:475px;top:1872px;font-family:"Montserrat",Arial,sans-serif;font-weight:500;font-size:20px;color:var(--red)}
/* insights */
.card{top:2390px;width:253px;height:250px;color:var(--white)}
.card .caption{position:absolute;left:22px;bottom:18px;font-size:13px;font-weight:600;line-height:18px}
.card.red{background:var(--red);padding:28px 24px}
.card.red .date{font-size:11px}
.card.red h4{font-size:14px;line-height:18px;margin:6px 0 12px}
.card.red p{font-size:10.5px;line-height:16px;opacity:.85}
.card.red .more{display:block;margin-top:18px;font-size:11px;font-weight:700}
/* contact */
.info{font-size:12px;line-height:20px;color:#444;display:flex;gap:16px;align-items:flex-start}
.social{left:510px;top:2874px;display:flex;gap:26px}
.social i{width:12px;height:12px;border-radius:50%;background:var(--red)}
.field{border:1px solid #bbb;height:35px;padding:8px 14px;font-size:12px;color:#999}
.submit{left:875px;top:3068px;width:138px;height:38px;background:var(--red);color:var(--white);font-family:"Montserrat",Arial,sans-serif;font-weight:700;font-size:14px;display:flex;align-items:center;justify-content:center}
.footer{left:0;top:3185px;width:1200px;height:58px;background:var(--footer);color:#aaa;font-size:12px;display:flex;align-items:center;justify-content:center}
</style>
</head>
<body>

<!-- 01 Home -->
<section class="abs hero" role="img" aria-label="Photo of consultants reviewing documents around a laptop in a meeting"></section>
<div class="abs brand"><span class="brand-mark"></span><span>Bluefinch Advisory Partners</span></div>
<nav class="abs nav"><span>HOME</span><span>THE WAY WE WORK</span><span>WHAT WE DO</span><span>OUR FOUNDER</span><span>INSIGHTS</span><span>CONTACT</span></nav>
<div class="abs hero-num">01</div>
<div class="abs dots" style="left:199px;top:252px"><i class="on" style="background:var(--red)"></i><i></i><i></i><i></i></div>
<h1 class="abs hero-title">WE ARE ORGANISATION &amp;<span>PEOPLE CONSULTING FIRM</span></h1>
<div class="abs slider">
  <b><svg width="8" height="8" viewBox="0 0 8 8"><path d="M5 1 2 4l3 3" stroke="#333" stroke-width="1.6" fill="none"/></svg></b>
  <i class="on"></i><i></i><i></i><i></i>
  <b><svg width="8" height="8" viewBox="0 0 8 8"><path d="M3 1l3 3-3 3" stroke="#333" stroke-width="1.6" fill="none"/></svg></b>
</div>

<!-- 02 The Way We Work -->
<div class="abs sec-num" style="left:140px;top:782px">02</div>
<h2 class="abs sec-title" style="left:216px;top:775px">THE WAY<br>WE WORK</h2>
<div class="abs dots" style="left:172px;top:826px"><i></i><i class="on"></i><i></i><i></i></div>
<div class="abs copy" style="left:465px;top:780px;width:555px">
  <p>Fusce ultricies orci ac feugiat suscipit leo massa sodales velit et scelerisque mi tortor at ipsum cligula augue bibendum accumsan vestibulum ut commodo</p>
  <p>nisl nec elit Praesent elementum elit at tellus nec ultricies sit amet porttitor mattis enim In massa libero interdum nec interdum vel blandit sed nulla In ullamcorper est eget tempor cursus neque mi consectetuer mi a ultricies massa est sed nisl Class aptent taciti sociosqu ad litora torquent per conubia nostra per inceptos hymenaeos Proin nulla arcu nonummy luctus dictum eget fermentum et lorem</p>
</div>

<!-- 03 What We Do -->
<svg class="abs" style="left:0;top:1100px" width="1200" height="605" viewBox="0 1100 1200 605" aria-hidden="true">
  <polygon points="0,1108 1200,1105 1200,1700 0,1695" fill="var(--red-soft)"/>
  <polygon points="0,1132 1200,1105 1200,1660 0,1682" fill="var(--red)"/>
</svg>
<div class="abs sec-num" style="left:140px;top:1217px;color:var(--white)">03</div>
<h2 class="abs sec-title" style="left:216px;top:1210px;color:var(--white)">WHAT WE DO</h2>
<div class="abs dots" style="left:172px;top:1258px"><i style="background:#eee"></i><i style="background:#555"></i><i style="background:#eee"></i><i style="background:#eee"></i></div>
<p class="abs copy" style="left:494px;top:1210px;width:520px;color:var(--white)">l blandit sed nulla In ullamcorper est eget tempor cursus neque mi consectetuer mi a ultricies massa est sed nisl Class aptent taciti sociosqu ad litora torquent per conubia nostra per</p>

<svg class="abs" style="left:0;top:1360px" width="1200" height="220" viewBox="0 1360 1200 220" aria-hidden="true">
  <g stroke="#fff" stroke-width="1.5" fill="none">
    <path d="M440 1381 V1455 H560"/><path d="M440 1550 V1488 H560"/>
    <path d="M780 1381 V1455 H660"/><path d="M780 1540 V1488 H660"/>
    <circle cx="610" cy="1470" r="48"/>
  </g>
  <g fill="#fff"><circle cx="440" cy="1381" r="4"/><circle cx="440" cy="1550" r="4"/><circle cx="780" cy="1381" r="4"/><circle cx="780" cy="1540" r="4"/></g>
</svg>
<div class="abs icon-ring" style="left:442px;top:1383px"></div>
<div class="abs icon-ring" style="left:442px;top:1490px"></div>
<div class="abs icon-ring" style="left:724px;top:1380px"></div>
<div class="abs icon-ring" style="left:724px;top:1488px"></div>
<div class="abs service left" style="left:170px;top:1372px"><h3>ORGANISATION DESIGN</h3><p>Donec dictum lectus non odio<br>Cras a ante vitae enim iaculis<br>aliquam Mauris nunc</p></div>
<div class="abs service left" style="left:170px;top:1508px"><h3>EMPLOYEE EXPERIENCE</h3><p>Donec dictum lectus non odio<br>Cras a ante vitae enim iaculis<br>aliquam Mauris nunc</p></div>
<div class="abs service" style="left:838px;top:1366px"><h3>CHANGE MANAGEMENT</h3><p>Donec dictum lectus non odio<br>Cras a ante vitae enim iaculis<br>aliquam Mauris nunc</p></div>
<div class="abs service" style="left:838px;top:1492px"><h3>EXECUTIVE COACHING</h3><p>Donec dictum lectus non odio<br>Cras a ante vitae enim iaculis<br>aliquam Mauris nunc quam</p></div>

<!-- 04 Our Founder -->
<div class="abs sec-num" style="left:140px;top:1737px">04</div>
<h2 class="abs sec-title" style="left:216px;top:1730px">OUR<br>FOUNDER</h2>
<div class="abs dots" style="left:172px;top:1780px"><i></i><i class="on"></i><i></i><i></i></div>
<div class="abs" role="img" aria-label="Portrait photo of the founder" style="left:205px;top:1862px;width:240px;height:240px;border-radius:50%;background:radial-gradient(circle at 45% 40%,#8a7f78,#4a4644 70%,#2d2b2a)"></div>
<div class="abs founder-name">FOUNDER NAME</div>
<div class="abs copy" style="left:475px;top:1908px;width:555px">
  <p>Fusce ultricies orci ac feugiat suscipit leo massa sodales velit et scelerisque mi tortor at ipsum cligula augue bibendum accumsan vestibulum ut commodo</p>
  <p>nisl nec elit Praesent elementum elit at tellus nec ultricies sit amet porttitor mattis enim In massa libero interdum nec interdum vel blandit sed nulla In ullamcorper est eget tempor cursus neque mi consectetuer mi a ultricies massa est sed nisl Class aptent taciti sociosqu ad litora torquent per conubia nostra per inceptos hymenaeos Proin nulla arcu nonummy luctus dictum eget fermentum et lorem</p>
</div>

<!-- 05 Insights -->
<svg class="abs" style="left:0;top:2150px" width="1200" height="615" viewBox="0 2150 1200 615" aria-hidden="true">
  <polygon points="0,2165 1200,2152 1200,2762 0,2762" fill="var(--light-grey)"/>
  <polygon points="0,2190 1200,2152 1200,2718 0,2755" fill="var(--mid-grey)"/>
</svg>
<div class="abs sec-num" style="left:140px;top:2272px;color:var(--white)">05</div>
<h2 class="abs sec-title" style="left:216px;top:2265px;color:#d5d5d5">INSIGHTS</h2>
<div class="abs dots" style="left:172px;top:2313px"><i style="background:#eee"></i><i style="background:#eee"></i><i style="background:#eee"></i><i style="background:#111"></i><i style="background:#eee"></i></div>
<p class="abs copy" style="left:465px;top:2255px;width:555px;color:var(--white)">l blandit sed nulla In ullamcorper est eget tempor cursus neque mi consectetuer mi a ultricies massa est sed nisl Class aptent taciti sociosqu ad litora torquent per conubia nostra per inceptos hymenaeos Proin.</p>

<article class="abs card" style="left:203px" role="img" aria-label="Photo of two businessmen in conversation">
  <div style="position:absolute;inset:0;background:linear-gradient(160deg,#7c8795,#3b3f47 60%,#22252a)"></div>
  <div class="caption">Curabitur iaculis tempus eros<br>Curabitur vel mi sit amet</div>
</article>
<article class="abs card red" style="left:480px">
  <span class="date">25 MARCH 2018</span>
  <h4>Donec dictum lectus non odio Cras ante vitae enim</h4>
  <p>Our latest thinking on how teams adapt when roles, rituals and structure change together.</p>
  <span class="more">READ MORE</span>
</article>
<article class="abs card" style="left:755px" role="img" aria-label="Photo of a business handshake">
  <div style="position:absolute;inset:0;background:linear-gradient(160deg,#b89a7a,#6d5a4a 55%,#3a322c)"></div>
  <div class="caption">Morbi diam mauris viverra in<br>gravida eu mattis</div>
</article>

<!-- 06 Contact -->
<div class="abs sec-num" style="left:147px;top:2795px;color:var(--grey-text)">06</div>
<h2 class="abs sec-title" style="left:216px;top:2788px;color:var(--red)">CONTACT</h2>
<div class="abs dots" style="left:174px;top:2838px"><i style="background:#111"></i><i style="background:#111"></i><i style="background:#111"></i><i style="background:#111"></i><i class="on"></i></div>

<div class="abs info" style="left:505px;top:2805px">
  <svg width="14" height="18" viewBox="0 0 14 18"><path d="M7 1a6 6 0 0 0-6 6c0 4.5 6 10 6 10s6-5.5 6-10a6 6 0 0 0-6-6z" fill="none" stroke="#666" stroke-width="1.4"/><circle cx="7" cy="7" r="2" fill="#666"/></svg>
  <span>48 HARLOW LANE #4B<br>TEXAS 75021 TX</span>
</div>
<div class="abs social"><i></i><i></i><i></i></div>
<div class="abs info" style="left:803px;top:2805px">
  <svg width="18" height="16" viewBox="0 0 18 16"><path d="M4 1l3 3-2 2a10 10 0 0 0 5 5l2-2 3 3-2 3C8 15 2 9 1 3z" fill="none" stroke="#666" stroke-width="1.3"/></svg>
  <span>512.555.0148</span>
</div>
<div class="abs info" style="left:803px;top:2838px">
  <svg width="18" height="14" viewBox="0 0 18 14"><rect x="1" y="1" width="16" height="12" fill="none" stroke="#666" stroke-width="1.3"/><path d="M1 1l8 7 8-7" fill="none" stroke="#666" stroke-width="1.3"/></svg>
  <span>INFO@BLUEFINCHADVISORY.COM</span>
</div>

<div class="abs field" style="left:232px;top:2930px;width:254px">Your Name</div>
<div class="abs field" style="left:495px;top:2930px;width:255px">Email address</div>
<div class="abs field" style="left:758px;top:2930px;width:255px">Phone number</div>
<div class="abs field" style="left:232px;top:2977px;width:781px;height:82px">Message</div>
<div class="abs submit">SUBMIT</div>

<footer class="abs footer">© 2018 COMPANY NAME &nbsp;ALL RIGHT RESERVED</footer>

</body>
</html>
```